Corbell Lending Partners - Real estate loans - need a business card with a logo

I need a logo and a business card that looks elegant - that looks as if it is a big stablish corporation - We do real estate loans, my goal is to brand myself with colors black background - gold or silver letters - some combination - Name of the company different color than the rest of the card -

```html
<!DOCTYPE html>
<html lang="en">
<head>
<meta charset="utf-8">
<title>Corbell Lending Partners – Business Card</title>
<link rel="stylesheet" href="https://fonts.googleapis.com/css2?family=Arimo:wght@400;700&display=swap">
<style>
  :root {
    --stage: #161616;
    --card-front: #1d1d1d;
    --card-back: #202020;
    --pattern-dark: #262626;
    --pattern-mid: #555555;
    --pattern-light: #8a8a8a;
    --silver: #d6d6d6;
    --silver-soft: #bdbdbd;
    --brand-grey: #8c8c8c;
    --gold: #c9a25a;
    --divider: #7a7a7a;
  }
  * { box-sizing: border-box; margin: 0; padding: 0; }
  html, body { width: 1200px; height: 900px; overflow: hidden; }
  body {
    background: var(--stage);
    font-family: "Arimo", Arial, sans-serif;
    position: relative;
  }
  .card {
    position: absolute;
    left: 250px;
    width: 700px;
    height: 400px;
    border-radius: 2px;
    overflow: hidden;
    box-shadow: 0 12px 30px rgba(0, 0, 0, 0.55);
  }
  .card--back { top: 35px; background: var(--card-back); }
  .card--front { top: 465px; background: var(--card-front); }

  .back-pattern {
    position: absolute;
    inset: 0;
    background:
      radial-gradient(ellipse 70% 80% at 50% 48%, var(--pattern-mid) 0%, transparent 75%),
      linear-gradient(125deg, var(--pattern-dark) 0%, var(--pattern-light) 45%, var(--pattern-mid) 60%, var(--pattern-dark) 100%);
  }
  .back-mark {
    position: absolute;
    left: 50%;
    top: 50%;
    transform: translate(-50%, -50%);
    display: flex;
    align-items: center;
    gap: 12px;
    color: var(--gold);
    font-weight: 700;
    font-size: 18px;
    letter-spacing: 3px;
    text-transform: uppercase;
    background: var(--card-back);
    padding: 14px 22px;
  }
  .back-mark .mark-square {
    width: 18px; height: 18px; background: var(--gold);
  }

  .brand {
    position: absolute;
    left: 60px;
    top: 120px;
    width: 240px;
    display: flex;
    flex-direction: column;
    align-items: center;
    gap: 18px;
  }
  .brand .mark-square {
    width: 70px; height: 70px; background: var(--brand-grey);
  }
  .brand-name {
    color: var(--brand-grey);
    font-weight: 700;
    font-size: 24px;
    line-height: 1.15;
    letter-spacing: 1.5px;
    text-transform: uppercase;
    text-align: center;
  }

  .divider {
    position: absolute;
    left: 335px;
    top: 85px;
    width: 2px;
    height: 210px;
    background: var(--divider);
  }

  .contact {
    position: absolute;
    left: 375px;
    top: 88px;
    right: 30px;
    color: var(--silver-soft);
  }
  .contact-name {
    color: var(--silver);
    font-weight: 700;
    font-size: 28px;
    letter-spacing: 1px;
    text-transform: uppercase;
    white-space: nowrap;
  }
  .contact-role {
    font-size: 17px;
    margin-top: 2px;
  }
  .contact-address {
    font-size: 18px;
    line-height: 1.3;
    margin-top: 18px;
  }
  .contact-list {
    list-style: none;
    margin-top: 10px;
    font-size: 18px;
    line-height: 1.55;
  }
  .contact-list li { display: flex; align-items: center; gap: 8px; }
  .contact-list svg { width: 13px; height: 13px; flex: none; }
</style>
</head>
<body>

  <section class="card card--back">
    <div class="back-pattern" role="img" aria-label="Repeating embossed monogram pattern in silver on black"></div>
    <div class="back-mark">
      <span class="mark-square"></span>
      <span>Corbell</span>
    </div>
  </section>

  <section class="card card--front">
    <div class="brand">
      <span class="mark-square"></span>
      <p class="brand-name">Corbell<br>Lending Partners</p>
    </div>

    <div class="divider"></div>

    <div class="contact">
      <h1 class="contact-name">Daniel Hargrove</h1>
      <p class="contact-role">Founder</p>
      <p class="contact-address">418 Linden Avenue<br>Colville, WA 99114</p>
      <ul class="contact-list">
        <li>
          <svg viewBox="0 0 16 16" fill="none" stroke="currentColor" stroke-width="1.6"><path d="M4 1.5l2.5 3-1.5 1.8a9 9 0 0 0 4.7 4.7l1.8-1.5 3 2.5-1.5 2.5C7 14 2 9 1.5 3z"/></svg>
          570 555 0182
        </li>
        <li>
          <svg viewBox="0 0 16 16" fill="none" stroke="currentColor" stroke-width="1.6"><rect x="1.5" y="3.5" width="13" height="9"/><path d="M1.5 3.5L8 9l6.5-5.5"/></svg>
          info@corbelllending.com
        </li>
        <li>
          <svg viewBox="0 0 16 16" fill="none" stroke="currentColor" stroke-width="1.4"><circle cx="8" cy="8" r="6.5"/><ellipse cx="8" cy="8" rx="3" ry="6.5"/><path d="M1.5 8h13"/></svg>
          www.corbelllending.com
        </li>
      </ul>
    </div>
  </section>

</body>
</html>
```